Business Card - high end, modern health care

Hey designers!

We need a double sided business card for the boutique, cutting edge physical therapy rehabilitation centre in Sydney's Northern Beaches.

With the most qualified physios in the area The Harbourview Motion Clinic does what other physiotherapy practices do not, we take our time with our patients giving them longer appointments, better physios and therefor faster results!

We guarantee that the service people receive at THMC will be unparalleled.

Hence we need a business card to reflect our modern, boutique, high end service. The final design needs to reflect that we are in a class of our own yet with the feel of beachside retreat.

Below I have attached our logo in both blue on white and white on blue. The exact colour is;
and the font that we have used in our logo is Tex Gyre Aventador.

I like the idea of the blue as the main colour as it is more eye catching and our signage onto the main road will be in this blue and in the interest of consistency across marketing the blue needs to be a part of the design. However I would appreciate a few designs onto a wooden background as this is a visual theme within the fitout of the practice.

The design needs to be of standard size (91x55mm).

Target Market(s)

We target people who have an end outcome in mind and those who have had poor experiences with other providers and ensure that everyone gets the care that they deserve with a premium service that is tailored to the individuals circumstances. As a premium service, the target market is highly educated, business and tech savvy with the additional target market of elderly people who have self funded their retirement and see value in paying for the best ongoing rehabilitation to maintain independence.

Industry/Entity Type

Physical Therapy

Contact Information for Business Card

Name, designation( Titled Musculoskeletal Physiotherapist... there will also be those in the company that have multiple designations ie 5 or 6 words long), phone number, email, facebook, instagram, address

Font styles to use
Sans Serif

Colors

Designer to choose colors to be used in the design.

Requirements
Must have
• Front - The logo as large as possible, blue or wooden theme, and all of the important details.
• Back - A blank space/lines on which to write appointment times (no "Appointment, date, time" etc.)
Nice to have
• facebook url
• logos for facebook and instagram
• Mini logos for the phone and email?

```html
<!DOCTYPE html>
<html lang="en">
<head>
<meta charset="utf-8">
<title>The Harbourview Motion Clinic — Business Card</title>
<link rel="stylesheet" href="https://fonts.googleapis.com/css2?family=Questrial&family=Work+Sans:wght@400;500&display=swap">
<style>
  :root {
    --backdrop: #202020;
    --card: #1a1a1a;
    --card-light: #262626;
    --brand-blue: #0d5bb5;
    --text-light: #f2f2f2;
  }
  * { box-sizing: border-box; margin: 0; padding: 0; }
  html, body {
    width: 1200px;
    height: 900px;
    overflow: hidden;
    background: var(--backdrop);
  }
  .sheet {
    width: 1200px;
    height: 900px;
    display: flex;
    flex-direction: column;
    align-items: center;
    justify-content: center;
    gap: 40px;
  }
  .card {
    position: relative;
    width: 640px;
    height: 387px;
    background: linear-gradient(135deg, var(--card) 0%, var(--card) 55%, var(--card-light) 100%);
    border-bottom: 6px solid var(--brand-blue);
    box-shadow: 0 12px 30px rgba(0, 0, 0, 0.55);
    overflow: hidden;
  }

  /* Back: centred brand */
  .card--brand {
    display: flex;
    flex-direction: column;
    align-items: center;
    justify-content: center;
    gap: 22px;
  }
  .brand-disc {
    width: 150px;
    height: 150px;
    border-radius: 50%;
    background: var(--brand-blue);
  }
  .brand-name {
    font-family: "Questrial", sans-serif;
    color: var(--brand-blue);
    text-transform: uppercase;
    text-align: center;
    line-height: 1.1;
  }
  .card--brand .brand-name { font-size: 24px; letter-spacing: 2px; }

  /* Front: details */
  .card--details {
    display: flex;
    align-items: center;
    padding: 0 40px 0 44px;
  }
  .card__identity {
    display: flex;
    align-items: center;
    gap: 12px;
    width: 300px;
  }
  .identity-disc {
    flex: none;
    width: 46px;
    height: 46px;
    border-radius: 50%;
    background: var(--brand-blue);
  }
  .card--details .brand-name { font-size: 21px; letter-spacing: 1px; text-align: left; }
  .card__divider {
    width: 2px;
    height: 170px;
    background: var(--brand-blue);
    margin: 0 26px 0 14px;
  }
  .card__contact {
    font-family: "Work Sans", sans-serif;
    color: var(--text-light);
    font-size: 14px;
    line-height: 1.45;
  }
  .person-name {
    font-family: "Questrial", sans-serif;
    color: var(--brand-blue);
    font-size: 25px;
    text-transform: uppercase;
    line-height: 1;
  }
  .person-role { font-size: 14px; margin-bottom: 12px; }
  .address { margin-bottom: 10px; }
  .contact-list { list-style: none; }
  .contact-list li { display: flex; align-items: center; gap: 8px; }
  .contact-icon { width: 12px; height: 12px; flex: none; }
  .social-links {
    position: absolute;
    left: 378px;
    bottom: 34px;
    display: flex;
    gap: 12px;
  }
  .social-dot {
    width: 16px;
    height: 16px;
    border-radius: 3px;
    background: var(--text-light);
  }
</style>
</head>
<body>
<main class="sheet">

  <section class="card card--brand" aria-label="Card back">
    <div class="brand-disc"></div>
    <p class="brand-name">The Harbourview<br>Motion Clinic</p>
  </section>

  <section class="card card--details" aria-label="Card front">
    <div class="card__identity">
      <div class="identity-disc"></div>
      <p class="brand-name">The Harbourview<br>Motion Clinic</p>
    </div>
    <div class="card__divider"></div>
    <div class="card__contact">
      <p class="person-name">Daniel Carter</p>
      <p class="person-role">Director</p>
      <p class="address">24 Ocean Parade, Suite 3,<br>Dee Why, NSW 2099</p>
      <ul class="contact-list">
        <li>
          <svg class="contact-icon" viewBox="0 0 12 12" aria-hidden="true"><path d="M3 1 L5 3.5 L4 5 Q5 7 7 8 L8.5 7 L11 9 L9.5 11 Q4 10.5 1 3 Z" fill="var(--brand-blue)"/></svg>
          +61 2 9000 4127
        </li>
        <li>
          <svg class="contact-icon" viewBox="0 0 12 12" aria-hidden="true"><rect x="1" y="2.5" width="10" height="7" fill="none" stroke="var(--brand-blue)" stroke-width="1.2"/><path d="M1 2.5 L6 6.5 L11 2.5" fill="none" stroke="var(--brand-blue)" stroke-width="1.2"/></svg>
          info@harbourviewmotion.com
        </li>
        <li>
          <svg class="contact-icon" viewBox="0 0 12 12" aria-hidden="true"><circle cx="6" cy="6" r="4.8" fill="none" stroke="var(--brand-blue)" stroke-width="1.2"/><path d="M1.2 6 H10.8 M6 1.2 Q3 6 6 10.8 M6 1.2 Q9 6 6 10.8" fill="none" stroke="var(--brand-blue)" stroke-width="1"/></svg>
          www.harbourviewmotion.com
        </li>
      </ul>
    </div>
    <div class="social-links" aria-label="Social profiles">
      <span class="social-dot"></span>
      <span class="social-dot"></span>
    </div>
  </section>

</main>
</body>
</html>
```